Require an amazing and engaging Home Page redesign! For New Startup!

We require a new design for our home page of www.quonto.com.au.

We want this to be in a similar theme to the current site, all other pages to remain unchanged however our marketing team have advised that the current home page (initial banner) is not engaging or "hooking" potential leads. I have attached "CRO Recommendations" from our marketing team as an idea to the issues with the Quonto site.
At the moment we would only like the issues on home page reviewed (Pages: 4 to 10).

I have attached an example from our marketing team as to an idea of how the front home page needs to look.

As an idea of what our competition is doing well please view zephrimo.com.au, trevalix.com.au (great engagement on home page top banner).

Quonto is a brand new concept for Australian new car buyers. Quonto allows a customer buying a new car to receive best price offer for their new car needs and finance requirements all on a sophisticated online dashboard. The dashboard even allows the customer to interact directly with the dealerships to negotiate the price online! (never offered before).

I've provided new logo, brand guidelines for colour and font scheme.

View the website to get an idea of what Quonto is all about and let's see what we can come up with.

Thanks.

Target Market(s)

Females, age between 21-35

Industry/Entity Type

Automotive

Number of Pages Required

1 page

Requirements
Must have
• Engaging initial banner. We want to see the banner as mocked up and provided but also maybe provide an option showing a large graphic as the banner that incorporates this "hook" for engagement.
• Minimal menu (no Need Help or Newsletter buttons) with new logo on left.
• As per design mockup. Looking for engaging banner.
• Why it Works benefits section - 3 to 4 key benefits
• Customer satisfaction/testimonial area
Nice to have
• As Seen On banner or icon somewhere - maybe near or under the "Get Offers' buttons? As we have been featured in the MORNING LARK

```html
<!DOCTYPE html>
<html lang="en">
<head>
<meta charset="utf-8">
<title>Quonto – Get car dealers and lenders to bid for your business</title>
<link href="https://fonts.googleapis.com/css2?family=Open+Sans:wght@400;600;700&display=swap" rel="stylesheet">
<style>
:root{
  --teal:#1b8c9b;
  --blue:#2d79b3;
  --navy:#1d5a86;
  --gold:#e3a42b;
  --btn:#27a8b1;
  --ink:#333a40;
  --muted:#8a9099;
  --line:#dfe3e7;
  --grey-bg:#f1f2f3;
  --why-bg:#2f76a8;
}
*{box-sizing:border-box;margin:0;padding:0}
html,body{width:1200px;height:3232px;overflow:hidden}
body{font-family:'Open Sans',Arial,sans-serif;color:var(--ink);background:#fff;position:relative}
.abs{position:absolute}

/* header */
.site-header{position:absolute;left:0;top:0;width:1200px;height:100px;background:#fff;border-bottom:1px solid var(--line)}
.brand{position:absolute;left:108px;top:30px;display:flex;align-items:center;gap:14px}
.brand-dot{width:40px;height:40px;border-radius:50%;background:var(--gold)}
.brand-name{font-size:34px;font-weight:700;color:var(--blue)}
.main-nav{position:absolute;left:446px;top:43px;display:flex;gap:42px;font-size:17px;color:#7d848b}
.phone{position:absolute;left:948px;top:40px;display:flex;align-items:center;gap:8px;font-size:19px;font-weight:700;color:var(--navy)}

/* hero */
.hero{position:absolute;left:0;top:100px;width:1200px;height:540px;background:linear-gradient(180deg,#f7f8f9,#eceef0)}
.hero-title{position:absolute;top:40px;width:100%;text-align:center;font-size:35px;font-weight:700;color:var(--teal)}
.hero-sub{position:absolute;top:88px;width:100%;text-align:center;font-size:24px;font-weight:400;color:var(--blue)}
.hero-card{position:absolute;left:134px;top:165px;width:933px;height:313px;background:#fff;border-radius:18px;box-shadow:0 4px 16px rgba(0,0,0,.12)}
.hero-photo{position:absolute;left:205px;top:140px;width:195px;height:338px;border-radius:90px 90px 0 0;background:linear-gradient(180deg,#c9a98a 0%,#b48a6c 35%,#5cc2e8 55%,#3fb0dc 100%)}
.step{position:absolute;width:220px;text-align:center;font-size:16px;line-height:1.45;color:#444}
.step-circle{width:120px;height:120px;border-radius:50%;margin:0 auto 18px;position:relative;display:flex;align-items:center;justify-content:center}
.step-num{position:absolute;left:6px;top:2px;font-size:20px;color:#fff}

/* featured */
.featured{position:absolute;left:0;top:640px;width:1200px;height:108px;background:#eeeff0;border-top:1px solid var(--line);border-bottom:1px solid var(--line)}
.featured-label{position:absolute;left:103px;top:42px;font-size:18px;color:#8a8f94}
.press-badge{position:absolute;top:36px;height:34px;background:#c9cdd1;border-radius:4px}

/* packages */
.section-title{position:absolute;width:100%;text-align:center;font-size:28px;font-weight:400}
.package{position:absolute;top:873px;width:317px;height:556px;background:#fff;border:1px solid var(--line);box-shadow:0 2px 6px rgba(0,0,0,.08)}
.package-photo{height:147px}
.package-head{margin:28px 20px 0;text-align:center;font-size:14.5px;font-weight:400;line-height:1.35;text-transform:uppercase;color:#333}
.package-list{list-style:none;margin:22px 0 0 40px;font-size:12px;color:#555}
.package-list li{position:relative;padding-left:18px;margin-bottom:10px}
.package-list li::before{content:"";position:absolute;left:2px;top:3px;width:5px;height:8px;border:solid var(--teal);border-width:0 2px 2px 0;transform:rotate(45deg)}
.price{position:absolute;left:30px;top:358px;font-size:27px;font-weight:600;color:var(--gold)}
.select{position:absolute;left:22px;width:271px;height:32px;border:1px solid #cfd3d7;border-radius:2px;font-size:11.5px;color:#666;padding:8px 10px}
.select::after{content:"";position:absolute;right:11px;top:12px;border:5px solid transparent;border-top-color:#555}
.select.plain::after{display:none}
.btn{position:absolute;height:44px;border-radius:8px;color:#fff;font-size:15px;font-weight:700;text-align:center;line-height:44px}
.btn-teal{background:var(--btn);box-shadow:0 3px 0 #1d8087}
.badge-popular{position:absolute;left:503px;top:847px;width:181px;height:44px;background:var(--gold);color:#fff;font-size:15px;font-weight:600;text-align:center;line-height:44px;clip-path:polygon(0 0,100% 0,94% 50%,100% 100%,0 100%,6% 50%)}

/* testimonials */
.reviews{position:absolute;left:0;top:1476px;width:1200px;height:539px;background:var(--grey-bg);border-top:1px solid var(--line)}
.review{position:absolute;top:120px;width:220px}
.avatar{width:78px;height:78px;border-radius:50%;background:linear-gradient(160deg,#d9b89a,#8b6b55);border:2px solid #fff}
.stars{margin-top:14px;color:var(--gold);font-size:17px;letter-spacing:2px}
.review h3{font-size:16px;font-weight:400;color:#333;margin-top:6px}
.review p{font-size:13px;color:#9aa0a6;line-height:1.45;margin-top:8px}
.review .who{font-size:13.5px;font-weight:600;color:var(--blue);margin-top:10px}
.review .city{font-size:12.5px;color:var(--blue);opacity:.8}
.rated{position:absolute;top:436px;width:100%;text-align:center;font-size:14px;color:#a3a8ad}

/* why it works */
.why{position:absolute;left:0;top:2015px;width:1200px;height:500px;background:linear-gradient(90deg,#2c6f9e,#3a85b8)}
.why-tab{position:absolute;left:388px;top:1975px;width:427px;height:100px;background:var(--why-bg);border-radius:50% 50% 0 0/80% 80% 0 0}
.why-title{position:absolute;top:1998px;width:100%;text-align:center;font-size:31px;font-weight:400;color:#fff}
.why-kicker{position:absolute;left:254px;top:2127px;font-size:26px;color:#fff}
.benefit{position:absolute;top:2200px;width:180px;text-align:center;color:#fff}
.benefit h4{font-size:17px;font-weight:400;margin-top:18px}
.benefit p{font-size:11.5px;line-height:1.55;margin-top:6px;font-weight:600}
.btn-gold{background:var(--gold);border:2px solid #fff;border-radius:24px}
.video{position:absolute;left:625px;top:2118px;width:487px;height:304px;border:3px solid #fff;background:linear-gradient(135deg,#6d7f8f,#b4bdc4 55%,#3d4a55)}

/* deals */
.deals-title{position:absolute;width:100%;text-align:center;font-size:27px;font-weight:400;line-height:1.55;color:#222}
.deal{position:absolute;top:2683px;width:240px;text-align:center}
.deal-photo{width:205px;height:128px;margin:0 auto;border-radius:40px 60px 14px 14px;background:linear-gradient(180deg,#eef0f2,#c9cdd1 60%,#9ea4aa)}
.deal h5{font-size:17px;font-weight:400;color:var(--blue);margin-top:34px}
.deal p{font-size:12.5px;color:#a0a6ab;margin-top:6px}
.deal .save{font-size:17.5px;font-weight:400;color:var(--gold);margin-top:12px}

/* footer */
.site-footer{position:absolute;left:0;top:3017px;width:1200px;height:215px;background:var(--navy);color:#fff;text-align:center}
.footer-links{margin-top:50px;font-size:15.5px}
.footer-links span{margin:0 8px}
.legal{margin-top:10px;font-size:13.5px;opacity:.85}
.social{display:flex;justify-content:center;gap:12px;margin-top:26px}
.social i{width:30px;height:30px;border-radius:50%;background:#fff;display:block}
</style>
</head>
<body>

<header class="site-header">
  <div class="brand"><span class="brand-dot"></span><span class="brand-name">Quonto</span></div>
  <nav class="main-nav"><span>How it works</span><span>Pricing</span><span>FAQ</span><span>Apply</span><span>Login</span></nav>
  <div class="phone">
    <svg width="22" height="22" viewBox="0 0 22 22"><rect width="22" height="22" rx="4" fill="#e3a42b"/><path d="M7 5l2.5 0 1 3-1.5 1.2a8 8 0 0 0 3.8 3.8L14 11.5l3 1v2.5c0 .8-.7 1.5-1.5 1.5C10 16.5 5.5 12 5.5 6.5 5.5 5.7 6.2 5 7 5z" fill="#fff"/></svg>
    1300 555 019
  </div>
</header>

<section class="hero">
  <h1 class="hero-title">A Revolution in Car Buying Has Arrived</h1>
  <p class="hero-sub">Get car dealers and lenders to bid for YOUR business today</p>
  <div class="hero-card"></div>
  <div class="hero-photo" role="img" aria-label="Smiling woman holding a blue cardboard car cut-out"></div>

  <div class="step" style="left:403px;top:211px">
    <div class="step-circle" style="background:radial-gradient(circle at 40% 35%,#f2c04f,#d9961f)">
      <span class="step-num">1</span>
      <svg width="52" height="52" viewBox="0 0 52 52" fill="none" stroke="#fff" stroke-width="3" stroke-linejoin="round"><path d="M8 24h8v20H8zM16 26l9-14c2-3 6-1 5 3l-2 8h12c3 0 4 3 3 5l-4 14c-1 2-2 3-4 3H16"/></svg>
    </div>
    Submit You Car or<br>Finance Needs
  </div>
  <div class="step" style="left:612px;top:211px">
    <div class="step-circle" style="background:radial-gradient(circle at 40% 35%,#4c9bd0,#23639a)">
      <span class="step-num">2</span>
      <svg width="52" height="52" viewBox="0 0 52 52" fill="none" stroke="#fff" stroke-width="3"><circle cx="26" cy="16" r="9"/><path d="M8 48c0-10 8-17 18-17s18 7 18 17M26 31l-3 8 3 5 3-5z"/></svg>
    </div>
    Dealerships<br>and lenders submit<br>their best offers
  </div>
  <div class="step" style="left:823px;top:211px">
    <div class="step-circle" style="background:radial-gradient(circle at 40% 35%,#2e6f99,#174b73)">
      <span class="step-num">3</span>
      <svg width="52" height="52" viewBox="0 0 52 52" fill="none" stroke="#fff" stroke-width="3" stroke-linejoin="round"><path d="M22 28V10c0-3 5-3 5 0v14l10 2c3 1 4 3 3 6l-3 12H22l-8-10c-2-3 1-6 4-4z"/><path d="M16 14a9 9 0 0 1 17 0"/></svg>
    </div>
    You choose the best<br>deal online and<br>exchange contact<br>details. It's that easy!
  </div>
  <svg class="abs" style="left:578px;top:245px" width="60" height="30" viewBox="0 0 60 30" fill="none" stroke="#9aa3ab" stroke-width="2"><path d="M2 26C15 4 40 2 54 12"/><path d="M46 8l8 4-6 7"/></svg>
  <svg class="abs" style="left:790px;top:245px" width="60" height="30" viewBox="0 0 60 30" fill="none" stroke="#9aa3ab" stroke-width="2"><path d="M2 26C15 4 40 2 54 12"/><path d="M46 8l8 4-6 7"/></svg>
</section>

<section class="featured">
  <span class="featured-label">As featured In</span>
  <span class="press-badge" style="left:262px;width:112px"></span>
  <span class="press-badge" style="left:404px;width:172px"></span>
  <span class="press-badge" style="left:617px;width:112px"></span>
  <span class="press-badge" style="left:780px;width:125px"></span>
  <span class="press-badge" style="left:950px;width:136px"></span>
</section>

<h2 class="section-title" style="top:786px;color:#1a1a1a;font-weight:600">Choose your Car to Get Started</h2>

<article class="package" style="left:82px">
  <div class="package-photo" role="img" aria-label="Woman waving from a red convertible" style="background:linear-gradient(135deg,#3d5a35,#8a3a30 55%,#c9463a)"></div>
  <h3 class="package-head">I just need the best deals<br>on a new car.</h3>
  <ul class="package-list"><li>3 Dealership BEST PRICE car quotes</li></ul>
  <div class="price">$140</div>
  <div class="select" style="top:404px">car Model</div>
  <div class="select" style="top:443px">car Make</div>
  <div class="btn btn-teal" style="left:82px;top:489px;width:150px">GET OFFERS</div>
</article>

<article class="package" style="left:435px">
  <div class="package-photo" role="img" aria-label="Smiling woman at the wheel of a car" style="background:linear-gradient(135deg,#6b7c86,#b98e72 55%,#3f4b55)"></div>
  <h3 class="package-head">I need the best deals on a new<br>car and finance.</h3>
  <ul class="package-list"><li>3 Dealership BEST PRICE car quotes</li><li>3 car finance quotes from our broker panel</li></ul>
  <div class="price">$179</div>
  <div class="select" style="top:404px">car Model</div>
  <div class="select" style="top:443px">car Make</div>
  <div class="btn btn-teal" style="left:82px;top:489px;width:150px">GET OFFERS</div>
</article>
<div class="badge-popular">Most Popular</div>

<article class="package" style="left:791px">
  <div class="package-photo" role="img" aria-label="Yellow sports car on a road" style="background:linear-gradient(135deg,#4a4f55,#e2b51c 50%,#6e6a5a)"></div>
  <h3 class="package-head">I just want the best deal on<br>my car finance.</h3>
  <ul class="package-list" style="margin-top:16px"><li>Perfect for NEW OR USED cars</li><li>Receive up to 3 live loan quotes</li><li>Guaranteed to beat Dealership finance</li><li>Quotes from our award-winning broker panel</li></ul>
  <div class="price" style="top:358px">$220</div>
  <div class="select plain" style="top:404px">$ &nbsp;Estimated Loan Amount</div>
  <div class="btn btn-teal" style="left:82px;top:489px;width:150px">GET OFFERS</div>
</article>

<section class="reviews">
  <h2 class="section-title" style="top:48px;font-size:26px;color:var(--blue)">See What Our Customer Says</h2>
  <svg class="abs" style="left:44px;top:228px" width="20" height="36" viewBox="0 0 20 36" fill="none" stroke="#b5bac0" stroke-width="3"><path d="M17 2L3 18l14 16"/></svg>
  <svg class="abs" style="left:1122px;top:228px" width="20" height="36" viewBox="0 0 20 36" fill="none" stroke="#b5bac0" stroke-width="3"><path d="M3 2l14 16L3 34"/></svg>

  <div class="review" style="left:108px">
    <div class="avatar" role="img" aria-label="Customer portrait"></div>
    <div class="stars">☆☆☆☆</div>
    <h3>Excellent- No Reservation</h3>
    <p>Arcu Morbi porta libero id ullamcorper nonummy nibh ligula pulvinar metus</p>
    <div class="who">- LIAM PORTER</div><div class="city">Sydney</div>
  </div>
  <div class="review" style="left:371px">
    <div class="avatar" role="img" aria-label="Customer portrait"></div>
    <div class="stars">☆☆☆☆</div>
    <h3>Awesome!</h3>
    <p>Arcu Morbi porta libero id ullamcorper nonummy nibh ligula pulvinar metus</p>
    <div class="who">- NADIA STONE</div><div class="city">NSW</div>
  </div>
  <div class="review" style="left:634px">
    <div class="avatar" role="img" aria-label="Customer portrait"></div>
    <div class="stars">☆☆☆☆</div>
    <h3>Professional</h3>
    <p>Arcu Morbi porta libero id ullamcorper nonummy nibh ligula pulvinar metus</p>
    <div class="who">- LIAM PORTER</div><div class="city">Sydney</div>
  </div>
  <div class="review" style="left:894px">
    <div class="avatar" role="img" aria-label="Customer portrait"></div>
    <div class="stars">☆☆☆☆</div>
    <h3>Best Customer Service</h3>
    <p>Arcu Morbi porta libero id ullamcorper nonummy nibh ligula pulvinar metus</p>
    <div class="who">- LIAM PORTER</div><div class="city">Sydney</div>
  </div>
  <p class="rated">Rated 9.3 out of 10 based on 302 Reviews</p>
</section>

<section class="why" aria-label="Why it Works"></section>
<div class="why-tab"></div>
<h2 class="why-title">Why it Works</h2>
<div class="why-kicker">SELLING A CAR?</div>

<div class="benefit" style="left:65px">
  <svg width="72" height="72" viewBox="0 0 72 72" fill="none" stroke="#fff" stroke-width="3"><path d="M36 6v30M42 11c-2-2-4-3-7-3-4 0-7 2-7 5s3 4 7 5 8 2 8 6-3 5-8 5c-3 0-6-1-8-3"/><path d="M12 62V50l6-10h36l6 10v12M12 52h48"/><circle cx="22" cy="56" r="3"/><circle cx="50" cy="56" r="3"/></svg>
  <h4>1. No Fees</h4>
  <p>We don't charge referral fees, giving you unbiased &amp; better pricing</p>
</div>
<div class="benefit" style="left:255px">
  <svg width="72" height="72" viewBox="0 0 72 72" fill="none" stroke="#fff" stroke-width="3"><circle cx="42" cy="18" r="13"/><path d="M36 18l5 5 9-10"/><path d="M12 62V50l6-10h36l6 10v12M12 52h48"/><circle cx="22" cy="56" r="3"/><circle cx="50" cy="56" r="3"/></svg>
  <h4>2. Bargaining Power</h4>
  <p>Drive the best bargain with our dashboard &amp; negotiating tool</p>
</div>
<div class="benefit" style="left:438px">
  <svg width="72" height="72" viewBox="0 0 72 72" fill="none" stroke="#fff" stroke-width="3"><rect x="36" y="6" width="30" height="16" rx="3" transform="rotate(-15 51 14)"/><path d="M8 62V50l6-10h36l6 10v12M8 52h48"/><circle cx="18" cy="56" r="3"/><circle cx="46" cy="56" r="3"/></svg>
  <h4>3. Ultimate Choice</h4>
  <p>We don't dealer discriminate! We have over 3,500 new car dealerships in our system</p>
</div>
<div class="btn btn-gold" style="left:260px;top:2408px;width:172px;height:48px;line-height:44px">GET OFFERS</div>

<div class="video" role="img" aria-label="Video still: salesman handing car keys to a smiling couple at a dealership">
  <svg class="abs" style="left:212px;top:120px" width="56" height="56" viewBox="0 0 56 56"><circle cx="28" cy="28" r="27" fill="#fff"/><path d="M22 17l18 11-18 11z" fill="#2f76a8"/></svg>
</div>

<h2 class="deals-title" style="top:2568px">Live Deals- Our Average clients saved<br>Nearly 14% off list Price</h2>

<div class="deal" style="left:89px">
  <div class="deal-photo" role="img" aria-label="Silver dual-cab utility vehicle"></div>
  <h5>Kestrel Trailmaster</h5><p>interdum vel blandit sed nulla</p><div class="save">Discount of $7,780</div>
</div>
<div class="deal" style="left:361px">
  <div class="deal-photo" role="img" aria-label="Silver dual-cab utility vehicle"></div>
  <h5>Halden Ute-X</h5><p>interdum vel blandit sed nulla</p><div class="save">Discount of $6,233</div>
</div>
<div class="deal" style="left:632px">
  <div class="deal-photo" role="img" aria-label="White hatchback" style="background:linear-gradient(180deg,#f4f5f6,#dfe2e5 60%,#a7acb1)"></div>
  <h5>Solano C3</h5><p>interdum vel blandit sed nulla</p><div class="save">Discount of $5,995</div>
</div>
<div class="deal" style="left:904px">
  <div class="deal-photo" role="img" aria-label="White sedan" style="background:linear-gradient(180deg,#f4f5f6,#dfe2e5 60%,#a7acb1)"></div>
  <h5>Veltra 3</h5><p>interdum vel blandit sed nulla</p><div class="save">Discount of $4,790</div>
</div>

<footer class="site-footer">
  <div class="footer-links">
    <span>How it works</span>|<span>Pricing</span>|<span>FAQ</span>|<span>Privacy Policy</span>|<span>Terms and Conditions</span>|<span>Car Reviews</span>|<span>Become a Supplier</span>
  </div>
  <p class="legal">Quonto Enterprises Pty Ltd T/A Quonto ABN 12 345 678 901</p>
  <div class="social"><i></i><i></i><i></i><i></i></div>
</footer>

</body>
</html>
```